Marvane Pour Over Coffee Filter Packaging Design

We are a brand new company starting to sell coffee related products. The coffee filter that we are about to sell will be copper color. We are working on the exact product picture, but a temporary one will be in uploaded files.We want the box to be simple, yet elegant and not too flashy. We prefer black, rose gold, white design, but are open to other designs. The uploaded files are just samples of what we like. "Marvane" means "owl" in French, we want an owl to be on the logo. Coffee related logo design is best, but we are open to other ideas. Size of this particular packaging is 14x14x12 cm

Target Market(s)

Online Retail

Industry/Entity Type

It Company

Logo Text

"Marvane Products" and "Marvane"

Other font styles liked:
• Your choice

Colors

Designer to choose colors to be used in the design.

Requirements
Must have
• Owl on the logo. Product description in a word file attached.
Nice to have
• Read product description

```html
<!DOCTYPE html>
<html lang="en">
<head>
<meta charset="utf-8">
<title>Marvane Pour Over Coffee Filter – Packaging</title>
<link href="https://fonts.googleapis.com/css2?family=Michroma&family=Montserrat:wght@400;500;700&display=swap" rel="stylesheet">
<style>
  :root {
    --page-bg: #f1f1f1;
    --panel-dark: #3a3a3a;
    --panel-dark-edge: #2e2e2e;
    --panel-light: #f7f7f7;
    --ink-dark: #2b2b2b;
    --ink-body: #3c3c3c;
    --ink-light: #e2e2e2;
    --title-grey: #bdbdbd;
    --rule: #8a8a8a;
    --wisdom-bg: #0e0e0e;
    --gold-light: #e9d2a6;
    --gold-mid: #c9a56b;
    --gold-deep: #8d6b3a;
  }
  * { box-sizing: border-box; margin: 0; padding: 0; }
  html, body { width: 1200px; height: 1200px; overflow: hidden; }
  body {
    background: var(--page-bg);
    font-family: "Montserrat", Arial, sans-serif;
    position: relative;
  }
  .box-net {
    position: absolute;
    left: 100px;
    top: 150px;
    width: 1000px;
    height: 900px;
    display: flex;
    box-shadow: 0 20px 40px rgba(0,0,0,0.12);
  }

  /* Side panel */
  .side-panel {
    width: 400px;
    height: 100%;
    background: var(--panel-light);
    color: var(--ink-dark);
    position: relative;
    padding: 50px 44px 0 44px;
  }
  .welcome p {
    font-size: 17px;
    line-height: 1.32;
    margin-bottom: 22px;
  }
  .welcome .lead { font-weight: 700; }
  .welcome .body { font-weight: 500; color: var(--ink-body); }
  .wisdom {
    position: absolute;
    left: 30px;
    bottom: 0;
    width: 260px;
    height: 340px;
    background: var(--wisdom-bg);
    color: #ffffff;
    padding: 26px 20px 0 22px;
  }
  .wisdom h3 {
    font-size: 18px;
    font-weight: 700;
    line-height: 1.3;
    margin-bottom: 22px;
  }
  .wisdom p {
    font-size: 17px;
    font-weight: 500;
    line-height: 1.32;
  }

  /* Front panel */
  .front-panel {
    width: 600px;
    height: 100%;
    background: var(--panel-dark);
    border-left: 2px solid var(--panel-dark-edge);
    position: relative;
    color: var(--ink-light);
  }
  .product-photo {
    position: absolute;
    left: 330px;
    top: 50px;
    width: 250px;
    height: 310px;
    border-radius: 6px;
    background: radial-gradient(ellipse at 50% 40%, var(--gold-light) 0%, var(--gold-mid) 50%, var(--gold-deep) 100%);
  }
  .headline {
    position: absolute;
    left: 40px;
    top: 230px;
    font-family: "Michroma", "Arial Black", sans-serif;
  }
  .headline .kicker {
    font-size: 14px;
    letter-spacing: 1px;
    color: #d8d8d8;
    margin-bottom: 6px;
  }
  .headline .title {
    font-size: 40px;
    line-height: 1.1;
    color: var(--title-grey);
    letter-spacing: 1px;
  }
  .instructions {
    position: absolute;
    left: 40px;
    right: 34px;
    top: 430px;
  }
  .instructions h2 {
    font-family: "Michroma", "Arial Black", sans-serif;
    font-size: 18px;
    font-weight: 400;
    color: #dcdcdc;
    margin-bottom: 8px;
  }
  .instructions ol {
    list-style: none;
    font-size: 14.5px;
    line-height: 1.5;
    color: #cfcfcf;
  }
  .footer-rule {
    position: absolute;
    left: 40px;
    right: 34px;
    top: 740px;
    height: 1px;
    background: var(--rule);
  }
  .brand-mark {
    position: absolute;
    left: 40px;
    top: 790px;
    display: flex;
    align-items: center;
    gap: 10px;
    font-weight: 700;
    font-size: 22px;
    color: var(--ink-light);
  }
  .brand-mark .dot {
    width: 14px;
    height: 14px;
    border-radius: 50%;
    background: var(--ink-light);
  }
</style>
</head>
<body>
  <main class="box-net">
    <section class="side-panel">
      <div class="welcome">
        <p class="lead">Hello there!</p>
        <p class="lead">Thank you for purchasing one of the Marvane products!</p>
        <p class="lead">We hope you enjoy it!</p>
        <p class="body">Here at Marvane, we like our coffee fresh and hot and so we strive to share our experience with you!</p>
        <p class="body">We have put together a few tips on how to make your coffee experience the best, so check it out!</p>
      </div>
      <aside class="wisdom">
        <h3>Word of Wisdom from the Marvane Team:</h3>
        <p>A good cup of coffee shared with a friend is like capturing happiness in a cup! Share the liquid gold (coffee that is) with others!</p>
      </aside>
    </section>

    <section class="front-panel">
      <div class="product-photo" role="img" aria-label="Product photo of the copper pour over coffee filter cone on its base"></div>
      <div class="headline">
        <p class="kicker">HIGH QUALITY</p>
        <p class="title">COFFEE<br>FILTER</p>
      </div>
      <div class="instructions">
        <h2>INSTRUCTIONS</h2>
        <ol>
          <li>1. Place filter on your favorite mug and fill with a desired amount of coffee, we recommend 2-3 teaspoons per one cup of coffee.</li>
          <li>2. Pre-infuse your coffee by pouring just enough hot water to allow water to soak through the grounds. Wait for 30 seconds.</li>
          <li>3. Pour desired amount of water onto your pre-infused coffee in circular motion. Be careful not to pour too much water at once.</li>
          <li>4. It should take about three minutes for a 6 ounce cup of coffee to finish dripping.</li>
          <li>5. Sit back and enjoy your cup of coffee!</li>
        </ol>
      </div>
      <div class="footer-rule"></div>
      <div class="brand-mark"><span class="dot"></span>Marvane</div>
    </section>
  </main>
</body>
</html>
```